"Beyond The Grey Harbor" Fictional Book Cover

BEYOND THE GREY HARBOR
By: Derek Falloway

Here's the intro .

"It had been nearly forty years since Tim Ashworth last went to the island from where he was raised. Three months earlier he never would have thought about ever coming back. But life is weird. Things happen quickly and plans change, especially when your very life is at stake. The reason he was going back wasn’t to see old friends...no, no, no. They’re all dead. Of all the kids he grew up with on the island who moved off, he’s the only one still alive. Why?"

Pretty much all just a Lumora book, by the way.

Target Market(s)

fiction readers

Requirements
Must have
• Somewhat of a dark, mysterious cover is what I'd like to see. Use your imagination. I've never written a fiction book before so I'm very open to ideas

Needs to have my name, DEREK FALLOWAY at the bottom. like my other books, all of which are non-fiction
Nice to have
• Mysterious is what I'm looking for. NOT A HORROR story though. More a guy who left the island years ago, but is being called back to escape the rat race of modern, consumerist culture.

Please remember this NEEDS to jump out as a thumbnail on Brevix as people are browsing. Mainly the WORDS need to stick out. Lighter words on a say a blue background.

If you want to try to use the attached pic, or something like this, to reflect an island in the cover, that'd be good.

I've also uploaded a couple images I purchased from Pictoravault, hopefully you can make something work with these.

```html
<!DOCTYPE html>
<html lang="en">
<head>
<meta charset="utf-8">
<title>Beyond The Grey Harbor – Derek Falloway</title>
<link href="https://fonts.googleapis.com/css2?family=Cinzel:wght@400;500&display=swap" rel="stylesheet">
<style>
  :root {
    --sky-top: #1d3f52;
    --sky-mid: #3b6c84;
    --sky-low: #46788f;
    --tree-dark: #1c2a24;
    --tree-mid: #2c3d33;
    --shore: #6f8383;
    --water-top: #2f4d66;
    --water-bottom: #1f3a52;
    --title: #ffffff;
    --title-glow: rgba(255, 255, 255, 0.55);
  }
  html, body {
    margin: 0;
    padding: 0;
    width: 750px;
    height: 1200px;
    overflow: hidden;
    background: var(--sky-top);
  }
  .cover {
    position: relative;
    width: 750px;
    height: 1200px;
    overflow: hidden;
  }
  .cover__scene {
    position: absolute;
    inset: 0;
    background:
      linear-gradient(to bottom,
        transparent 0, transparent 640px,
        var(--tree-dark) 700px,
        var(--tree-mid) 880px,
        #3a4a40 960px,
        var(--shore) 985px,
        #4b5a58 1010px,
        var(--tree-dark) 1030px,
        var(--water-top) 1040px,
        var(--water-bottom) 1200px),
      linear-gradient(to bottom,
        var(--sky-top) 0,
        var(--sky-mid) 420px,
        var(--sky-low) 640px);
  }
  .cover__title {
    position: absolute;
    left: 0;
    right: 0;
    top: 108px;
    margin: 0;
    text-align: center;
    font-family: "Cinzel", serif;
    font-weight: 400;
    color: var(--title);
    text-shadow: 0 0 8px var(--title-glow), 0 0 18px rgba(255,255,255,0.25);
    line-height: 1;
  }
  .cover__title span {
    display: block;
    white-space: nowrap;
  }
  .title-line--one  { font-size: 136px; }
  .title-line--two  { font-size: 92px; margin-top: 26px; }
  .title-line--three{ font-size: 186px; margin-top: 16px; }
  .title-line--four { font-size: 138px; margin-top: 8px; }
  .cover__author {
    position: absolute;
    left: 0;
    right: 0;
    top: 1084px;
    margin: 0;
    text-align: center;
    font-family: "Cinzel", serif;
    font-weight: 400;
    font-size: 58px;
    color: var(--title);
    white-space: nowrap;
  }
</style>
</head>
<body>
  <main class="cover">
    <div class="cover__scene" role="img" aria-label="Dusky view across the water to a wooded island shore with white cottages among the trees and a rocky beach"></div>
    <h1 class="cover__title">
      <span class="title-line--one">BEYOND</span>
      <span class="title-line--two">THE</span>
      <span class="title-line--three">GREY</span>
      <span class="title-line--four">HARBOR</span>
    </h1>
    <p class="cover__author">Derek Falloway</p>
  </main>
</body>
</html>
```